female esthetician looking for an impact business card

I an an expert in skin care industry with high experience in NYC.I want my business card to look professional , an impact at first look. I do want a combination between white and gold . I believe the font will be great if is gold.. The Fonts are also important. MIRABELA COSTINA (SKIN CARE BOUTIQUE)

THIS SHOULD BE THE BUSINESS NAME, and should be placed on th eback of the card.
IN front m, the name MIRABELA COSTINA - ESTHETCIAN

BY APPOINTMENTS ONLY: 518.240.7136

Target Market(s)

HIGH END CLIENTELE

Contact Information for Business Card

iT WILL BE on a luxury paper. I neeed the wow feeling

Requirements
Should not have
• pictures

```html
<!DOCTYPE html>
<html lang="en">
<head>
<meta charset="utf-8">
<title>Mirabela Costina – Business Card</title>
<link rel="stylesheet" href="https://fonts.googleapis.com/css2?family=Lato:wght@400;700&display=swap">
<style>
  :root {
    --backdrop: #5b5b5b;
    --card: #110f0f;
    --gold: #e9bd23;
    --ink-light: #f1f1f1;
    --rule: #6b5a22;
  }
  html, body {
    margin: 0;
    padding: 0;
    width: 1200px;
    height: 802px;
    overflow: hidden;
    background: var(--backdrop);
    font-family: "Lato", sans-serif;
  }
  .stage {
    position: relative;
    width: 1200px;
    height: 802px;
  }
  .card {
    position: absolute;
    top: 274px;
    width: 443px;
    height: 265px;
    background: var(--card);
  }
  .card--front { left: 136px; }
  .card--back { left: 624px; }

  /* front */
  .front-mark {
    position: absolute;
    left: 20px;
    top: 112px;
    width: 192px;
    text-align: center;
    color: var(--gold);
    font-weight: 700;
    font-size: 15px;
    letter-spacing: 1px;
    line-height: 1.3;
  }
  .front-divider {
    position: absolute;
    left: 222px;
    top: 77px;
    width: 1px;
    height: 112px;
    background: var(--rule);
  }
  .details {
    position: absolute;
    left: 244px;
    top: 74px;
    color: var(--ink-light);
    font-size: 11px;
    line-height: 1.25;
  }
  .details__name {
    margin: 0;
    color: var(--gold);
    font-weight: 700;
    font-size: 15.5px;
    line-height: 1.1;
    letter-spacing: -0.2px;
  }
  .details__role {
    margin: 0 0 4px;
    font-size: 11px;
  }
  .details__note {
    margin: 0 0 1px;
    color: var(--gold);
    font-size: 9.5px;
    letter-spacing: 0.6px;
  }
  .contact {
    list-style: none;
    margin: 0 0 6px;
    padding: 0;
  }
  .contact li {
    display: flex;
    align-items: center;
    gap: 4px;
    margin-bottom: 2px;
    font-size: 11px;
  }
  .contact li.contact__phone { font-size: 12.5px; }
  .contact svg { width: 10px; height: 10px; fill: var(--gold); flex: none; }
  .address { margin: 0; font-size: 11px; line-height: 1.2; }

  /* back */
  .back-dot {
    position: absolute;
    left: 50%;
    top: 82px;
    width: 44px;
    height: 44px;
    margin-left: -22px;
    border-radius: 50%;
    background: var(--gold);
  }
  .back-name {
    position: absolute;
    left: 0;
    right: 0;
    top: 172px;
    margin: 0;
    text-align: center;
    color: var(--gold);
    font-weight: 400;
    font-size: 23px;
    letter-spacing: 2px;
  }
  .back-tagline {
    position: absolute;
    left: 0;
    right: 0;
    top: 201px;
    margin: 0;
    padding-left: 6px;
    text-align: center;
    color: var(--ink-light);
    font-size: 11px;
    letter-spacing: 6px;
    word-spacing: 6px;
  }
</style>
</head>
<body>
<main class="stage">
  <section class="card card--front">
    <div class="front-mark">MIRABELA<br>COSTINA</div>
    <div class="front-divider"></div>
    <div class="details">
      <h1 class="details__name">MIRABELA COSTINA</h1>
      <p class="details__role">ESTHETICIAN</p>
      <p class="details__note">BY APPOINTMENTS ONLY</p>
      <ul class="contact">
        <li class="contact__phone">
          <svg viewBox="0 0 10 10" aria-hidden="true"><path d="M1 3.2C1 2 2.5 1 5 1s4 1 4 2.2V4H6.8V3H3.2v1H1zM2.2 5h5.6l1 4H1.2z"/></svg>
          518.240.7136
        </li>
        <li>
          <svg viewBox="0 0 10 10" aria-hidden="true"><path d="M0.5 2h9v6h-9zM1.2 2.6 5 5.6l3.8-3V3.2L5 6.2 1.2 3.2z"/></svg>
          HELLO@MCBOUTIQUE.COM
        </li>
        <li>
          <svg viewBox="0 0 10 10" aria-hidden="true"><circle cx="5" cy="5" r="4.5"/></svg>
          WWW.MCBOUTIQUE.COM
        </li>
      </ul>
      <p class="address">214 LUMEN STREET, SUITE 5<br>NEW YORK, NY 10021</p>
    </div>
  </section>

  <section class="card card--back">
    <div class="back-dot"></div>
    <h2 class="back-name">MIRABELA COSTINA</h2>
    <p class="back-tagline">SKIN CARE BOUTIQUE</p>
  </section>
</main>
</body>
</html>
```